Buch-/E-Book-Cover für Kinderbuch zum spielerischen Umgang zwischen Kind und Hund
Zielgruppe
Die Zielgruppe sind Kinder die lernen möchten mit Ihrem Hund besser zu spielen, verstehen und erziehen. Es ist ein Kinderbuch und das Buch soll dementsprechend 'kinderlicher' gestaltet sein.
Ich habe kein eigenes Konzept für das Cover mir derzeitig überlegt und ich werde die erstellten Cover bei meiner Zielgruppe testen und danach den Gewinner küren.
In diesem Buch handelt sich um ein Sachbuch zum Thema Hundeerziehung für Kinder. Ich möchte Ihnen die Inhaltsangabe, Vorwort und Buchrückseite mitteilen. Das Buch werde ich auf Lesekorb.de veröffentlichen. Außerdem möchte ich Ihnen die 2 größten Konkurrenten vorstellen.
Das Vorwort:
Vorwort
Der Hund ist für das Kind mehr als nur ein vierbeiniger Hausgenosse mit Kuschelfaktor, er ist ein echter Partner zum Spielen und Lernen. Mit den passenden Ideen gestaltet sich der Alltag mit dem Tier richtig spannend. Sowohl Kind als auch Hund entwickeln sich Schritt für Schritt weiter und wachsen immer mehr zusammen. Für Jungen und Mädchen gibt es vielfältige Möglichkeiten, sich mit ihrem Vierbeiner zu beschäftigen. Kreative Rollenspiele gehören ebenso dazu wie das Lernen von Kunststücken, das Training von Intelligenz und Geschicklichkeit und das Basteln schöner Spielsachen. Lassen Sie sich von diesem Buch inspirieren und von den Fähigkeiten Ihrer Kinder und Hunde überraschen!
Gliederung:
Einleitung und Grundlegendes
1. Warum spielen Hunde und Kinder?
Gemeinsamkeiten zwischen Kind und Welpe
Die Vorteile einer engen Hund-Kind-Beziehung
Kind und Hund – das absolute Dream-Team?
Welcher Hund passt zum Kind?
Voraussetzungen für sicheres Spielen
2. Kreative Spiele
Kreative Beschäftigung mit dem Hund – darf das sein?
Rollenspiele mit Hunden
Das richtige Alter für Rollenspiele
Beispiele für typische Rollenspiele im Kindesalter
Tierische Rollenspiele – vom Kind zum Hund
Eigene Kommandos erfi..
Aufgabenstellung
Der Titel vom Buch lautet: Komm zu uns! Wo Kleine den Vierbeiner kennen, führen und mit ihm toben dürfen.
Das sind die 2 größten Konkurrenten https://www.lesekorb.example/titel/4718
https://www.lesekorb.example/titel/5923
Das sind Cover auf dem Englisch sprachigen Markt die ich sehr gut finde
1. https://www.readbasket.example/item/8841
2. https://www.readbasket.example/item/3307

```html
<!DOCTYPE html>
<html lang="de">
<head>
<meta charset="utf-8">
<title>Komm zu uns! – Buchcover</title>
<link rel="stylesheet" href="https://fonts.googleapis.com/css2?family=Sniglet:wght@800&family=Mali:wght@600;700&display=swap">
<style>
  :root {
    --stage: #eef1f3;
    --sky: #a8cfe0;
    --sky-deep: #8fbdd2;
    --cloud: #ffffff;
    --title-blue: #7fb6d0;
    --ink: #2b2f33;
    --heading-brown: #6a3b22;
    --photo-warm: #8a6a55;
    --photo-cool: #b9d7e4;
  }
  * { box-sizing: border-box; margin: 0; padding: 0; }
  html, body { width: 1200px; height: 800px; overflow: hidden; }
  body {
    background: var(--stage);
    position: relative;
    font-family: "Mali", "Comic Sans MS", cursive;
  }
  .cover-spread {
    position: absolute;
    left: 180px; top: 100px;
    width: 840px; height: 600px;
    display: flex;
    box-shadow: 0 10px 30px rgba(0,0,0,.15);
  }
  .back-cover, .front-cover {
    position: relative;
    width: 400px; height: 600px;
    background: var(--sky);
    overflow: hidden;
  }
  .spine {
    width: 40px; height: 600px;
    background: var(--sky-deep);
  }
  .cloud-band {
    position: absolute;
    left: 0; top: 0; width: 100%; height: 70px;
    background: linear-gradient(to bottom, rgba(255,255,255,.85), rgba(255,255,255,0));
  }
  .foreword {
    position: absolute;
    left: 36px; top: 80px; width: 330px;
    color: var(--ink);
  }
  .foreword-heading {
    font-family: "Sniglet", "Arial Rounded MT Bold", sans-serif;
    font-weight: 800;
    color: var(--heading-brown);
    font-size: 28px;
    margin: 0 0 18px 40px;
  }
  .foreword-text {
    font-weight: 700;
    font-size: 15.5px;
    line-height: 1.55;
    text-align: center;
  }
  .title-band {
    position: absolute;
    left: 20px; top: 78px; width: 360px; height: 150px;
    background: var(--cloud);
    border-radius: 14px 40px 18px 36px;
  }
  .book-title {
    position: absolute;
    left: 20px; top: 88px; width: 360px;
    text-align: center;
    font-family: "Sniglet", "Arial Rounded MT Bold", sans-serif;
    font-weight: 800;
    color: var(--title-blue);
    font-size: 54px;
    line-height: 1.1;
    text-transform: uppercase;
    letter-spacing: 1px;
  }
  .book-subtitle {
    position: absolute;
    left: 30px; top: 248px; width: 340px;
    text-align: center;
    font-weight: 700;
    font-size: 17px;
    line-height: 1.45;
    color: var(--ink);
  }
  .cover-photo {
    position: absolute;
    left: 40px; top: 340px;
    width: 320px; height: 260px;
  }
</style>
</head>
<body>
  <main class="cover-spread">
    <section class="back-cover">
      <div class="cloud-band" role="img" aria-label="Weiße Wolken am Himmel"></div>
      <div class="foreword">
        <h2 class="foreword-heading">Vorwort</h2>
        <p class="foreword-text">Der Hund ist für das Kind mehr als nur ein vierbeiniger Hausgenosse mit Kuschelfaktor, er ist ein echter Partner zum Spielen und Lernen. Mit den passenden Ideen gestaltet sich der Alltag mit dem Tier richtig spannend. Sowohl Kind als auch Hund entwickeln sich Schritt für Schritt weiter und wachsen immer mehr zusammen. Für Jungen und Mädchen gibt es vielfältige Möglichkeiten, sich mit ihrem Vierbeiner zu beschäftigen. Kreative Rollenspiele gehören ebenso dazu wie das Lernen von Kunststücken, das Training von Intelligenz und Geschicklichkeit und das Basteln schöner Spielsachen. Lassen Sie sich von diesem Buch inspirieren und von den Fähigkeiten Ihrer Kinder und Hunde überraschen!</p>
      </div>
    </section>
    <div class="spine"></div>
    <section class="front-cover">
      <div class="cloud-band" role="img" aria-label="Weiße Wolken am Himmel"></div>
      <div class="title-band"></div>
      <h1 class="book-title">Komm<br>zu uns!</h1>
      <p class="book-subtitle">Wo Kleine den Vierbeiner kennen, führen und mit ihm toben dürfen.</p>
      <svg class="cover-photo" viewBox="0 0 320 260" role="img" aria-label="Foto: Husky und Kind mit Weihnachtsmütze schauen sich an">
        <defs>
          <linearGradient id="photoTone" x1="0" y1="0" x2="1" y2="0">
            <stop offset="0" stop-color="var(--photo-warm)"/>
            <stop offset="1" stop-color="var(--photo-cool)"/>
          </linearGradient>
        </defs>
        <rect width="320" height="260" fill="url(#photoTone)"/>
      </svg>
    </section>
  </main>
</body>
</html>
```